Varnik Holdings — Business Card Design Brief
Overview
Design a double-sided business card for Varnik Holdings that highlights our two service arms: Varnik Communications (telecommunications) and Varnik Energy (business energy solutions). The card should feel smart and stand out when handed to clients.

Objectives
Showcase our areas of specialty clearly.
Reflect the overall Varnik / Varnik Holdings brand while acknowledging both arms.
Explore using both logos (Communications + Energy) or one unified logo, depending on the design.

Deliverables
One double-sided business card design (front + back).

Content & Copy
Front (preferred): Logo: Varnik / Varnik Holdings
Descriptor: Business Communications | Business Energy
Back:My contact details and company details
Core products: Business Mobile • Telephony • Internet • Business Energy Solutions

Brand & Visual Direction
We have a group logo currently tailored more toward telecoms, plus a separate Varnik Energy logo.
Please explore layouts that use both logos or just one, whichever works best.
Color: I wouldn't mind seeing an option using our the Blue/Purple gradient from our website (varnik-example.co.uk), but also open to non-gradient approaches and other colours..

Overall look: Smart, modern, and distinctive.
Format & Print Specs
Double-sided business card format. (Use a standard size

Must-Haves
Front: Varnik wording or Varnik Holdings wording with atleast 1 logo also on front “Business Communications | Business Energy.”

Back: Contact + company details and core products.
A design that stands out while remaining professional.

Nice-to-Have Options
A gradient version using our site’s Blue/Purple gradient.
A non-gradient version.
A dual-logo treatment versus a single-logo treatment.

Thanks
Owen

```html
<!DOCTYPE html>
<html lang="en">
<head>
<meta charset="utf-8">
<title>Varnik Holdings — Business Card</title>
<link rel="stylesheet" href="https://fonts.googleapis.com/css2?family=Montserrat:wght@700&family=Roboto:wght@400&display=swap">
<style>
  :root{
    --page:#e9e9e9;
    --navy:#1e1a6e;
    --accent:#1a8fe0;
    --ink:#3a3a3a;
    --white:#ffffff;
    --sky:#0ab4e2;
    --deep:#0c5bd0;
  }
  *{margin:0;padding:0;box-sizing:border-box}
  html,body{width:1200px;height:1200px;overflow:hidden;background:var(--page)}
  body{position:relative;font-family:"Roboto",Arial,sans-serif}
  .card{position:absolute;left:256px;width:688px;height:394px;overflow:hidden}
  .card-front{top:158px;background:var(--white)}
  .card-back{top:654px;background:linear-gradient(180deg,var(--sky) 0%,var(--deep) 100%)}

  .brand{position:absolute;left:119px;top:92px;width:214px;height:180px}
  .brand-dot{position:absolute;left:2px;top:0;width:92px;height:92px;border-radius:50%;background:var(--accent)}
  .brand-name{position:absolute;left:0;top:118px;font-family:"Montserrat",Arial,sans-serif;font-weight:700;font-size:52px;line-height:1;color:var(--navy);letter-spacing:1px}

  .divider{position:absolute;left:363px;top:81px;width:1px;height:206px;background:#cfcfcf}

  .person{position:absolute;left:387px;top:90px}
  .person-name{font-family:"Montserrat",Arial,sans-serif;font-weight:700;font-size:26px;color:var(--navy);line-height:1}
  .person-role{font-size:15px;color:var(--accent);margin-top:6px}
  .address{position:absolute;left:387px;top:160px;font-size:16px;line-height:21px;color:var(--ink)}
  .contacts{position:absolute;left:387px;top:213px;list-style:none;font-size:16px;color:var(--ink)}
  .contacts li{display:flex;align-items:center;height:20.5px}
  .contacts svg{width:14px;height:14px;margin-right:10px;fill:var(--navy)}

  .products{position:absolute;left:0;right:0;top:324px;text-align:center;font-size:17px;color:#222}
  .band{position:absolute;left:0;top:362px;width:688px;height:32px}
  .website{position:absolute;right:44px;top:368px;font-size:16px;color:var(--white)}

  .arm{position:absolute;top:0;height:394px;width:344px}
  .arm-comms{left:0}
  .arm-energy{left:345px}
  .arm-mark{position:absolute;left:50%;top:140px;transform:translateX(-50%);display:flex;align-items:center;gap:12px}
  .arm-ring{width:52px;height:52px;border-radius:50%;border:5px solid var(--white)}
  .arm-name{font-family:"Roboto",Arial,sans-serif;font-size:34px;color:var(--white);letter-spacing:2px}
  .arm-caption{position:absolute;left:0;right:0;top:264px;text-align:center;font-size:16px;color:var(--white);letter-spacing:.3px}
  .arm-comms .arm-caption{left:-20px;right:20px}
  .arm-energy .arm-caption{left:-20px;right:20px}
  .back-divider{position:absolute;left:344px;top:114px;width:1px;height:166px;background:rgba(255,255,255,.7)}
</style>
</head>
<body>

<section class="card card-front" aria-label="Card front">
  <div class="brand">
    <span class="brand-dot"></span>
    <span class="brand-name">VARNIK</span>
  </div>
  <span class="divider"></span>

  <div class="person">
    <p class="person-name">DANIEL REEVE</p>
    <p class="person-role">President</p>
  </div>
  <p class="address">42 Harbour Row<br>Leeds, United Kingdom LS1 4DP</p>
  <ul class="contacts">
    <li><svg viewBox="0 0 24 24"><path d="M6.6 10.8a15.2 15.2 0 0 0 6.6 6.6l2.2-2.2a1 1 0 0 1 1-.25 11.4 11.4 0 0 0 3.6.6 1 1 0 0 1 1 1V20a1 1 0 0 1-1 1A17 17 0 0 1 3 4a1 1 0 0 1 1-1h3.5a1 1 0 0 1 1 1c0 1.25.2 2.45.6 3.6a1 1 0 0 1-.25 1z"/></svg>0113 496 0721</li>
    <li><svg viewBox="0 0 24 24"><path d="M7 1h10a2 2 0 0 1 2 2v18a2 2 0 0 1-2 2H7a2 2 0 0 1-2-2V3a2 2 0 0 1 2-2zm0 3v15h10V4z"/></svg>07700 900 418</li>
    <li><svg viewBox="0 0 24 24"><path d="M2 5h20v14H2zm2 2v.4l8 5.6 8-5.6V7l-8 5.6z"/></svg>info@varnik-example.co.uk</li>
  </ul>

  <p class="products">Business Mobile &nbsp;•&nbsp; Telephony &nbsp;•&nbsp; Internet &nbsp;•&nbsp; Business Energy Solutions</p>

  <svg class="band" viewBox="0 0 688 32" preserveAspectRatio="none">
    <defs>
      <linearGradient id="stripe" x1="0" x2="1" y1="0" y2="0">
        <stop offset="0" stop-color="#1a6fd8"/>
        <stop offset=".55" stop-color="#0ab4e2"/>
        <stop offset="1" stop-color="#1a6fd8"/>
      </linearGradient>
    </defs>
    <rect x="0" y="0" width="688" height="32" fill="#1e1a6e"/>
    <polygon points="0,0 443,0 432,14 0,14" fill="url(#stripe)"/>
    <polygon points="0,14 432,14 427,20 0,20" fill="#ffffff"/>
  </svg>
  <p class="website">www.varnik-example.co.uk</p>
</section>

<section class="card card-back" aria-label="Card back">
  <div class="arm arm-comms">
    <div class="arm-mark"><span class="arm-ring"></span><span class="arm-name">VARNIK</span></div>
    <p class="arm-caption">BUSINESS COMMUNICATIONS</p>
  </div>
  <span class="back-divider"></span>
  <div class="arm arm-energy">
    <div class="arm-mark"><span class="arm-ring"></span><span class="arm-name">VARNIK</span></div>
    <p class="arm-caption">BUSINESS ENERGY</p>
  </div>
</section>

</body>
</html>
```